Business Card Design Project

- makeup artist business card

- original and creative

- Elegant design

- Feel free to come out with cool designs but stick to being elegant and attractive

- Design relates to makeup

- includes name, occupation, contact numbers, email, website

- regular size business card

- round corner card

- double sided

- on 1 side it should just have the website name in the center " moonveilstudio.net "

Industry/Entity Type

Business

Requirements
Must have
• Delia Marsh
Makeup Artist
USA: +1 (415)772-0461
Singapore: +65 82307915
deliamarsh@moonveilstudio.net
www.moonveilstudio.net
Should not have
• nothing cartoon looking.
Pictures of makeup being grab from the internet.. Examples: eyes or lips.

```html
<!DOCTYPE html>
<html lang="en">
<head>
<meta charset="utf-8">
<title>Delia Marsh — Makeup Artist Business Card</title>
<link rel="stylesheet" href="https://fonts.googleapis.com/css2?family=Arimo:wght@400;700&family=Tinos:wght@700&display=swap">
<style>
  :root {
    --page-bg: #f3ecee;
    --plum-light: #9c2c72;
    --plum: #8a2466;
    --plum-dark: #74205a;
    --band-dark: #8b2667;
    --band-light: #c04f8e;
    --white: #ffffff;
    --card-white: #fbfbfb;
    --card-grey: #e6e6e6;
    --divider: rgba(255,255,255,0.75);
  }
  * { margin: 0; padding: 0; box-sizing: border-box; }
  html, body {
    width: 1200px; height: 951px; overflow: hidden;
    background: var(--page-bg);
    font-family: "Arimo", Arial, sans-serif;
  }
  .stage {
    width: 1200px; height: 951px;
    display: flex; flex-direction: column;
    align-items: center; justify-content: center; gap: 60px;
  }
  .card {
    width: 630px; height: 360px;
    border-radius: 26px;
    position: relative; overflow: hidden;
    box-shadow: 0 10px 24px rgba(80, 20, 55, 0.22);
  }

  /* Front side */
  .card-front {
    background: radial-gradient(ellipse at 45% 45%, var(--plum-light) 0%, var(--plum) 55%, var(--plum-dark) 100%);
    display: flex; align-items: center; justify-content: center;
  }
  .site-name {
    font-size: 26px; font-weight: 400; letter-spacing: 2.5px; color: var(--white);
  }

  /* Back side */
  .card-back {
    background: linear-gradient(180deg, var(--card-white) 0%, var(--white) 40%, var(--card-grey) 100%);
  }
  .info-band {
    position: absolute; left: 0; right: 0; top: 92px; height: 170px;
    display: flex;
  }
  .identity {
    width: 240px; background: var(--band-dark);
    display: flex; flex-direction: column; align-items: flex-end; justify-content: center;
    padding-right: 20px; color: var(--white);
  }
  .identity .person {
    font-family: "Tinos", "Times New Roman", serif; font-weight: 700; font-size: 23px;
  }
  .identity .role { font-size: 16px; margin-top: 4px; letter-spacing: .3px; }
  .contacts {
    flex: 1; background: var(--band-light);
    display: flex; align-items: center; padding-left: 16px;
  }
  .contacts .divider {
    width: 1.5px; height: 62px; background: var(--divider); margin-right: 16px;
  }
  .contacts ul { list-style: none; color: var(--white); font-size: 16px; line-height: 20px; letter-spacing: .2px; }
</style>
</head>
<body>
  <main class="stage">
    <section class="card card-front" aria-label="Business card front">
      <p class="site-name">www.moonveilstudio.net</p>
    </section>

    <section class="card card-back" aria-label="Business card back">
      <div class="info-band">
        <div class="identity">
          <h1 class="person">Delia Marsh</h1>
          <p class="role">Makeup Artist</p>
        </div>
        <div class="contacts">
          <span class="divider" aria-hidden="true"></span>
          <ul>
            <li>USA: +1 (415)772-0461</li>
            <li>Singapore: +65 82307915</li>
            <li>deliamarsh@moonveilstudio.net</li>
            <li>www.moonveilstudio.net</li>
          </ul>
        </div>
      </div>
    </section>
  </main>
</body>
</html>
```